Brell Stone Company Business Cards

Front and Back Business Card - logo and text setup - cool design. I need workable photoshop or illustrator files so I can setup each employee card with design that is created
Updates

Hi everyone, thank you for the great entries. Please no more white and blue cards - there are so many already - black and silver only now please. thanks!

Target Market(s)

Construction Industry - Facility Managers

Industry/Entity Type

Construction

Contact Information for Business Card

I really like contemporary simplistic looks - clean neat....not opposed to seeing some black backrounds

Requirements
Must have
• Logo/website address with design on front only - www.brellstone-example.com (logo attached)
• Back:
• Name/Title/Company Address/Phone/email address
Nice to have
• Cool design
Should not have
• Nothing gimmicky like Fire or Water - since we are a Fire Protection company - it has all been done

```html
<!DOCTYPE html>
<html lang="en">
<head>
<meta charset="utf-8">
<title>Brell Stone Company — Business Cards</title>
<link href="https://fonts.googleapis.com/css2?family=Source+Sans+3:wght@400;600;700;800&display=swap" rel="stylesheet">
<style>
  :root {
    --bg: #e9e7e4;
    --navy: #1f3f77;
    --orange: #ee4a33;
    --dark-1: #7a7b7d;
    --dark-2: #2c2c2e;
    --white: #ffffff;
    --ink-light: #f2f2f2;
  }
  * { box-sizing: border-box; margin: 0; padding: 0; }
  html, body { width: 1200px; height: 918px; overflow: hidden; }
  body {
    background: var(--bg);
    font-family: "Source Sans 3", Arial, sans-serif;
    position: relative;
  }
  .card {
    position: absolute;
    left: 250px;
    width: 700px;
    height: 400px;
    overflow: hidden;
    box-shadow: 0 6px 18px rgba(0,0,0,.18);
  }
  .card-front { top: 40px; background: linear-gradient(120deg, var(--dark-1), var(--dark-2) 75%); }
  .card-back  { top: 478px; background: var(--white); }

  .edge-band { position: absolute; top: 0; bottom: 0; width: 16px; }
  .edge-band.navy { left: 0; background: var(--navy); }
  .edge-band.orange { right: 0; background: var(--orange); }

  .front-panel {
    position: absolute;
    left: 150px; top: 70px;
    width: 400px; height: 260px;
    background: var(--white);
    border-radius: 60px;
    display: flex; flex-direction: column;
    align-items: center; justify-content: center;
    gap: 18px;
  }
  .wordmark {
    font-weight: 800;
    color: var(--navy);
    letter-spacing: -1px;
    line-height: 1;
  }
  .front-panel .wordmark { font-size: 62px; }
  .website { color: var(--orange); font-weight: 700; font-size: 26px; }

  .back-shape { position: absolute; inset: 0; }
  .back-logo { position: absolute; right: 60px; top: 96px; }
  .back-logo .wordmark { font-size: 60px; }

  .holder { position: absolute; left: 50px; top: 34px; color: var(--white); }
  .holder-name { font-size: 40px; font-weight: 700; line-height: 1.05; }
  .holder-title { font-size: 27px; font-weight: 400; color: var(--ink-light); }

  .contact-list { position: absolute; left: 44px; top: 190px; list-style: none; color: var(--white); }
  .contact-list li { display: flex; align-items: flex-start; gap: 16px; font-size: 22px; font-weight: 600; line-height: 1.15; margin-bottom: 16px; }
  .contact-icon { flex: 0 0 28px; width: 28px; height: 28px; border-radius: 50%; background: var(--white); display: flex; align-items: center; justify-content: center; }
  .fax { position: absolute; left: 380px; top: 344px; color: var(--white); font-size: 22px; font-weight: 600; }
</style>
</head>
<body>

<section class="card card-front" aria-label="Card front">
  <div class="edge-band navy"></div>
  <div class="edge-band orange"></div>
  <div class="front-panel">
    <div class="wordmark">brellstone</div>
    <div class="website">www.brellstone-example.com</div>
  </div>
</section>

<section class="card card-back" aria-label="Card back">
  <svg class="back-shape" width="700" height="400" viewBox="0 0 700 400" aria-hidden="true">
    <defs>
      <linearGradient id="backDark" x1="0" y1="0" x2="1" y2="1">
        <stop offset="0" stop-color="#7a7b7d"/>
        <stop offset="0.8" stop-color="#2c2c2e"/>
      </linearGradient>
    </defs>
    <path fill="url(#backDark)" d="M0 0 H330 Q360 0 362 40 L362 120 Q360 160 330 170 Q318 180 340 188 L410 198 Q440 204 442 240 L446 330 Q450 362 480 340 L520 268 Q540 246 560 270 L590 340 Q602 358 625 342 L660 312 Q690 296 692 330 L700 400 H0 Z"/>
    <rect x="0" y="0" width="16" height="400" fill="#1f3f77"/>
  </svg>

  <div class="holder">
    <div class="holder-name">Mr. RK</div>
    <div class="holder-title">Owner</div>
  </div>

  <ul class="contact-list">
    <li>
      <span class="contact-icon"><svg width="14" height="16" viewBox="0 0 14 16"><path fill="#ee4a33" d="M7 0a6 6 0 0 0-6 6c0 4.5 6 10 6 10s6-5.5 6-10a6 6 0 0 0-6-6zm0 8.5a2.5 2.5 0 1 1 0-5 2.5 2.5 0 0 1 0 5z"/></svg></span>
      <span>48 Harbor Works Road<br>Millbrook, NY 10000</span>
    </li>
    <li>
      <span class="contact-icon"><svg width="16" height="12" viewBox="0 0 16 12"><rect x="1" y="1" width="14" height="10" fill="none" stroke="#ee4a33" stroke-width="1.6"/><path d="M1 1l7 6 7-6M1 11l5-5M15 11l-5-5" fill="none" stroke="#ee4a33" stroke-width="1.4"/></svg></span>
      <span>info@brellstone-example.com</span>
    </li>
    <li>
      <span class="contact-icon"><svg width="14" height="14" viewBox="0 0 14 14"><path fill="#ee4a33" d="M3 0l2.5 3.2-1.4 1.7a8 8 0 0 0 5 5l1.7-1.4L14 11l-1.6 2.4C6 14 0 8 .6 1.6z"/></svg></span>
      <span>T: (555) 014-2210</span>
    </li>
  </ul>

  <div class="fax">F: (555) 014-2211</div>

  <div class="back-logo"><div class="wordmark">brellstone</div></div>
</section>

</body>
</html>
```